Mother's Day Sale Banner Ad For Jewelry Site

We are looking for a designer to design a banner on our website advertising our Mother's Day Sale. I have enclosed a few pieces of jewelry we would like used in the ad. The ad size needs to be 1187 × 400. The ad should say:

Mother's Day Sale - Save 15% with Promo Code: LOVEMOM

Jewelry

```html
<!DOCTYPE html>
<html lang="en">
<head>
<meta charset="utf-8">
<title>Mother's Day Sale Banner</title>
<link rel="stylesheet" href="https://fonts.googleapis.com/css2?family=Anton&family=Open+Sans:wght@600;700&display=swap">
<style>
  :root {
    --berry: #c9004f;
    --berry-deep: #86002f;
    --maroon: #7a0f2c;
    --burst: #f6d23d;
    --white: #ffffff;
    --band: #ececec;
    --photo-light: #f7f3ea;
    --photo-cream: #efe3c8;
    --photo-hair: #e2c48a;
    --photo-shirt: #f1e04a;
    --gold-light: #f4f1ea;
    --gold: #d9b561;
  }
  * { margin: 0; padding: 0; box-sizing: border-box; }
  html, body { width: 1200px; height: 404px; overflow: hidden; background: var(--white); }
  .banner {
    position: relative;
    width: 1200px;
    height: 404px;
    overflow: hidden;
    background: radial-gradient(ellipse at 62% 40%, var(--berry) 0%, #b3004a 45%, var(--berry-deep) 100%);
    font-family: "Open Sans", sans-serif;
  }
  .hero-shape { position: absolute; left: 0; top: 0; }
  .headline-kicker {
    position: absolute;
    left: 646px; top: 44px;
    color: var(--white);
    font-weight: 600;
    font-size: 35px;
    letter-spacing: -0.3px;
    text-shadow: 2px 2px 3px rgba(80, 0, 25, 0.5);
  }
  .headline-sale {
    position: absolute;
    left: 640px; top: 80px;
    color: var(--white);
    font-family: "Anton", sans-serif;
    font-size: 120px;
    line-height: 1;
    letter-spacing: 1px;
    text-shadow: 7px 7px 0 rgba(70, 0, 20, 0.55);
  }
  .discount-badge { position: absolute; left: 870px; top: 18px; }
  .discount-save {
    position: absolute;
    left: 932px; top: 30px;
    color: var(--berry);
    font-family: "Anton", sans-serif;
    font-size: 36px;
    line-height: 1.2;
    letter-spacing: 1px;
    transform: rotate(-7deg);
  }
  .discount-value {
    position: absolute;
    left: 918px; top: 86px;
    color: var(--maroon);
    font-family: "Anton", sans-serif;
    font-size: 96px;
    line-height: 1;
    transform: rotate(-4deg);
  }
  .discount-percent {
    position: absolute;
    left: 1020px; top: 92px;
    color: var(--maroon);
    font-family: "Open Sans", sans-serif;
    font-weight: 600;
    font-size: 28px;
    line-height: 1;
  }
  .product-band {
    position: absolute;
    left: 516px; top: 237px;
    width: 684px; height: 99px;
    background: var(--band);
    display: flex;
    align-items: center;
    gap: 24px;
    padding-left: 48px;
  }
  .product-photo {
    width: 138px; height: 86px;
    background: radial-gradient(circle at 50% 50%, var(--gold) 0%, #e7d3a0 35%, var(--gold-light) 70%);
  }
  .promo-code {
    position: absolute;
    left: 654px; top: 350px;
    color: var(--white);
    font-size: 29px;
    font-weight: 600;
  }
</style>
</head>
<body>
  <div class="banner">
    <svg class="hero-shape" width="600" height="404" viewBox="0 0 600 404" role="img" aria-label="Photo of a smiling mother in a yellow top and her young daughter looking at a laptop together">
      <defs>
        <linearGradient id="heroFill" x1="0" y1="0" x2="0.3" y2="1">
          <stop offset="0" stop-color="var(--photo-light)"/>
          <stop offset="0.35" stop-color="var(--photo-cream)"/>
          <stop offset="0.55" stop-color="var(--photo-hair)"/>
          <stop offset="0.8" stop-color="var(--photo-shirt)"/>
          <stop offset="1" stop-color="#f3e88a"/>
        </linearGradient>
      </defs>
      <path d="M0 0 H482 C565 100 578 300 540 404 H0 Z" fill="#e9c9d6"/>
      <path d="M0 0 H462 C545 100 558 300 520 404 H0 Z" fill="url(#heroFill)"/>
    </svg>

    <div class="headline-kicker">Mother’s Day</div>
    <div class="headline-sale">SALE</div>

    <svg class="discount-badge" width="212" height="212" viewBox="-106 -106 212 212" aria-hidden="true">
      <polygon fill="var(--burst)" points="100,0 85,13.4 95.1,30.9 76.6,39 80.9,58.8 60.8,60.8 58.8,80.9 39,76.6 30.9,95.1 13.4,85 0,100 -13.4,85 -30.9,95.1 -39,76.6 -58.8,80.9 -60.8,60.8 -80.9,58.8 -76.6,39 -95.1,30.9 -85,13.4 -100,0 -85,-13.4 -95.1,-30.9 -76.6,-39 -80.9,-58.8 -60.8,-60.8 -58.8,-80.9 -39,-76.6 -30.9,-95.1 -13.4,-85 0,-100 13.4,-85 30.9,-95.1 39,-76.6 58.8,-80.9 60.8,-60.8 80.9,-58.8 76.6,-39 95.1,-30.9 85,-13.4"/>
    </svg>
    <div class="discount-save">SAVE</div>
    <div class="discount-value">15</div>
    <div class="discount-percent">%</div>

    <div class="product-band">
      <div class="product-photo" role="img" aria-label="Gold rope rings with diamond crossover"></div>
      <div class="product-photo" role="img" aria-label="Gold and diamond band ring"></div>
      <div class="product-photo" role="img" aria-label="Gold crab brooch with pink stones"></div>
      <div class="product-photo" role="img" aria-label="Gold ring with carved coral"></div>
    </div>

    <div class="promo-code">PROMO CODE: LOVEMOM</div>
  </div>
</body>
</html>
```